New Innovative Counselling and psychotherapy Service needs Business Card design

Keep it simple and professional. On one side, just company name and logo (perhaps in all blue) and maybe a tag line.

On other side (all white) my name and Qualifications in centre

Industry/Entity Type

Health And Wellness

Contact Information for Business Card

Dara Whelby
Counsellor & Psychotherapist
BSc (Psychol.), BA, Dip. (Couns. & Psych.), PG.Cert (CBT), FGTrK, ONRE

I will also require Mobile no, Email and web site address of which I'll pass on to final designer.

Font styles to use
Sans Serif

Requirements
Must have
• My Logo Only and please use the colours in logo that is in it.
Should not have
• Any other images

```html
<!DOCTYPE html>
<html lang="en">
<head>
<meta charset="utf-8">
<title>Brightwell Lane – Business Card</title>
<link rel="stylesheet" href="https://fonts.googleapis.com/css2?family=Montserrat:wght@400&family=Roboto:wght@400;500;700&display=swap">
<style>
  :root {
    --page-bg: #e8e5e1;
    --card-bg: #f5f5f3;
    --card-edge: #dcdcda;
    --brand-blue: #3a9ccf;
    --brand-green: #7ab648;
    --ink-dark: #333638;
    --ink-body: #45484a;
  }
  * { margin: 0; padding: 0; box-sizing: border-box; }
  html, body {
    width: 1200px;
    height: 1054px;
    overflow: hidden;
    background: var(--page-bg);
  }
  .business-card {
    position: absolute;
    left: 80px;
    top: 214px;
    width: 1040px;
    height: 626px;
    background: var(--card-bg);
    border: 1px solid var(--card-edge);
    border-radius: 4px;
    font-family: "Roboto", Arial, sans-serif;
    color: var(--ink-body);
  }
  .brand {
    position: absolute;
    left: 37px;
    top: 56px;
    display: flex;
    align-items: center;
    gap: 30px;
  }
  .brand-dot {
    width: 150px;
    height: 150px;
    border-radius: 50%;
    background: var(--brand-blue);
    flex: none;
  }
  .brand-name {
    font-family: "Montserrat", Arial, sans-serif;
    font-weight: 400;
    font-size: 72px;
    line-height: 0.98;
    color: var(--ink-dark);
    letter-spacing: -0.5px;
  }
  .person {
    position: absolute;
    left: 44px;
    top: 288px;
  }
  .person-name {
    font-weight: 700;
    font-size: 41px;
    color: var(--brand-blue);
    line-height: 1.2;
    margin-bottom: 8px;
  }
  .person-role,
  .person-credentials {
    font-size: 24px;
    line-height: 32px;
    color: var(--ink-body);
  }
  .person-credentials { width: 470px; }
  .contact-list {
    position: absolute;
    left: 48px;
    top: 468px;
    list-style: none;
  }
  .contact-item {
    display: flex;
    align-items: center;
    gap: 22px;
    height: 40px;
    font-size: 25px;
    color: var(--ink-dark);
  }
  .contact-icon {
    width: 20px;
    height: 20px;
    flex: none;
    fill: var(--brand-green);
  }
</style>
</head>
<body>
  <section class="business-card">
    <div class="brand">
      <span class="brand-dot"></span>
      <div class="brand-name">Brightwell<br>Lane</div>
    </div>

    <div class="person">
      <h1 class="person-name">Dara Whelby</h1>
      <p class="person-role">Counsellor &amp; Psychotherapist</p>
      <p class="person-credentials">BSc (Psychol.), BA, Dip. (Couns. &amp; Psych.), &nbsp;PG.Cert (CBT), FGTrK, ONRE</p>
    </div>

    <ul class="contact-list">
      <li class="contact-item">
        <svg class="contact-icon" viewBox="0 0 20 20" aria-hidden="true">
          <path d="M2 7c0-2 3-4 8-4s8 2 8 4v1h-4V6.5H6V8H2z"/>
          <path d="M5 9h10l2 8H3z"/>
        </svg>
        <span>2468 135 7900</span>
      </li>
      <li class="contact-item">
        <svg class="contact-icon" viewBox="0 0 20 20" aria-hidden="true">
          <path d="M1 4h18v12H1z M2.5 5.5 10 11l7.5-5.5" stroke="#f5f5f3" stroke-width="1.4"/>
        </svg>
        <span>dara.w@BrightwellLane.com</span>
      </li>
      <li class="contact-item">
        <svg class="contact-icon" viewBox="0 0 20 20" aria-hidden="true">
          <circle cx="10" cy="10" r="9"/>
          <path d="M1 10h18 M10 1c-4 4-4 14 0 18 M10 1c4 4 4 14 0 18" fill="none" stroke="#f5f5f3" stroke-width="1.2"/>
        </svg>
        <span>www.BrightwellLane.com</span>
      </li>
    </ul>
  </section>
</body>
</html>
```